Business cards and stationary design

We just completed the design of our new logo and we need to print new business cards and letterhead for our nonprofit. We are looking for a fresh new design that shows off our new logo. On letterhead, we must have a column on the right or left to include our Board of Directors (up to 45 names) (see attachment)

Industry/Entity Type

Non-Profit

Contact Information for Business Card

Standard business card with name, title, Company name, mailing address phone numbers, email address and website. Tagline on back "Bringing the homeless home"

Font styles to use
Sans Serif

Requirements
Must have
• include pertinent information above
• new logo
• fonts compatible with logo
• should use logo colors only
Nice to have
• tag lines

```html
<!DOCTYPE html>
<html lang="en">
<head>
<meta charset="utf-8">
<title>Harbor Home Alliance – Business Card</title>
<link href="https://fonts.googleapis.com/css2?family=Roboto+Mono:wght@400;700&display=swap" rel="stylesheet">
<style>
  :root {
    --backdrop: #141414;
    --card: #2a2829;
    --gold: #f7b52a;
    --teal: #1b8ba3;
    --red: #e5202b;
    --divider: #6a6868;
  }
  * { margin: 0; padding: 0; box-sizing: border-box; }
  html, body {
    width: 1200px;
    height: 900px;
    overflow: hidden;
    background: var(--backdrop);
    font-family: "Roboto Mono", "Consolas", monospace;
  }
  .stage {
    position: relative;
    width: 1200px;
    height: 900px;
  }
  .card {
    position: absolute;
    top: 290px;
    width: 540px;
    height: 320px;
    background: var(--card);
  }
  .card--front { left: 40px; }
  .card--back { left: 620px; }

  /* Front */
  .brand-block {
    position: absolute;
    left: 36px;
    top: 0;
    width: 200px;
    height: 100%;
    display: flex;
    align-items: center;
    gap: 10px;
  }
  .brand-dot {
    flex: none;
    width: 14px;
    height: 14px;
    border-radius: 50%;
    background: var(--red);
  }
  .brand-name {
    color: var(--teal);
    font-size: 21px;
    line-height: 1.2;
    font-weight: 400;
  }
  .divider {
    position: absolute;
    left: 262px;
    top: 70px;
    width: 1px;
    height: 180px;
    background: linear-gradient(to bottom, transparent, var(--divider), transparent);
  }
  .contact {
    position: absolute;
    left: 290px;
    top: 82px;
    color: var(--teal);
    font-size: 13px;
    line-height: 1.45;
  }
  .contact__name {
    color: var(--gold);
    font-weight: 700;
    font-size: 18px;
    line-height: 1.15;
  }
  .contact__title { margin-bottom: 8px; }
  .contact__line {
    display: flex;
    align-items: center;
    gap: 6px;
  }
  .contact__line svg { width: 11px; height: 11px; flex: none; }
  .contact__address { margin-top: 12px; }

  /* Back */
  .brand-lockup {
    position: absolute;
    inset: 0;
    display: flex;
    flex-direction: column;
    align-items: center;
    justify-content: center;
    gap: 10px;
  }
  .brand-lockup__row {
    display: flex;
    align-items: center;
    gap: 12px;
  }
  .card--back .brand-name { font-size: 28px; }
  .card--back .brand-dot { width: 18px; height: 18px; }
  .tagline {
    color: var(--red);
    font-size: 13px;
    letter-spacing: 0.5px;
    padding-top: 6px;
    border-top: 1px solid var(--red);
  }
</style>
</head>
<body>
<main class="stage">
  <section class="card card--front">
    <div class="brand-block">
      <span class="brand-dot"></span>
      <span class="brand-name">harbor home alliance</span>
    </div>
    <div class="divider"></div>
    <div class="contact">
      <p class="contact__name">daniel moreland</p>
      <p class="contact__title">managing director</p>
      <p class="contact__line">
        <svg viewBox="0 0 12 12"><path fill="var(--red)" d="M2 1h3l1 3-1.5 1a6 6 0 0 0 2.5 2.5L8 6l3 1v3a1 1 0 0 1-1 1A9 9 0 0 1 1 2a1 1 0 0 1 1-1z"/></svg>
        444 555 0192
      </p>
      <p class="contact__line">
        <svg viewBox="0 0 12 12"><rect x="1" y="2.5" width="10" height="7" fill="var(--red)"/><path d="M1 2.5l5 4 5-4" fill="none" stroke="var(--card)" stroke-width="1"/></svg>
        hello@harborhome.org
      </p>
      <p class="contact__line">
        <svg viewBox="0 0 12 12"><circle cx="6" cy="6" r="5" fill="var(--red)"/><path d="M1 6h10M6 1c-2.5 3-2.5 7 0 10M6 1c2.5 3 2.5 7 0 10" fill="none" stroke="var(--card)" stroke-width="0.8"/></svg>
        www.harborhome.org
      </p>
      <p class="contact__address">88 Lantern Street,<br>Portside, 20417</p>
    </div>
  </section>

  <section class="card card--back">
    <div class="brand-lockup">
      <div class="brand-lockup__row">
        <span class="brand-dot"></span>
        <span class="brand-name">harbor home alliance</span>
      </div>
      <p class="tagline">bringing the homeless home</p>
    </div>
  </section>
</main>
</body>
</html>
```